Velmora Systems Website

Website design for our company: Velmora Systems.
The website should look fresh and IT focused. Please have a look at http://www.velmorasystems.example.au/ for our current design. We want something fresh and new, professional looking, in WordPress so we can easily make changes.

It Company

```html
<!DOCTYPE html>
<html lang="en">
<head>
<meta charset="utf-8">
<title>Velmora Systems</title>
<link href="https://fonts.googleapis.com/css2?family=Arimo:ital,wght@0,400;0,700;1,400&display=swap" rel="stylesheet">
<style>
:root{
  --green:#00b159;
  --green-dark:#009a4d;
  --ink:#111;
  --text:#555;
  --white:#fff;
  --footer:#3b3b3b;
  --footer-text:#d8d8d8;
  --rule:#cfcfcf;
}
*{box-sizing:border-box;margin:0;padding:0}
html,body{width:927px;height:1200px;overflow:hidden;background:var(--white)}
body{position:relative;font-family:"Arimo",Arial,sans-serif;color:var(--text)}
.abs{position:absolute}
.site-header{position:absolute;left:0;top:0;width:927px;height:58px;background:var(--green)}
.brand{position:absolute;left:132px;top:17px;display:flex;align-items:center;gap:8px;color:var(--white);font-size:17px;font-weight:700}
.brand-dot{width:22px;height:22px;border-radius:50%;background:var(--white)}
.main-nav a{position:absolute;top:24px;color:var(--white);font-size:10px;text-decoration:none;transform:translateX(-50%);white-space:nowrap}
.hero{position:absolute;left:0;top:58px;width:927px;height:335px;background:linear-gradient(120deg,#1d5fa8 0%,#3d8fd6 30%,#6c7680 55%,#2f76c2 80%,#174f96 100%)}
.hero-arrow{position:absolute;top:146px;width:37px;height:37px;border-radius:50%;border:2px solid rgba(255,255,255,.55)}
.remote{position:absolute;left:172px;top:262px;width:583px;height:51px;background:var(--white)}
.remote-label{position:absolute;left:24px;top:18px;font-size:13px;color:var(--ink)}
.remote-input{position:absolute;left:134px;top:12px;width:318px;height:27px;border:1px solid #aaa;border-radius:2px;font-size:9.5px;color:#888;padding:8px 11px}
.remote-btn{position:absolute;left:460px;top:12px;width:104px;height:26px;background:var(--green);color:var(--white);font-size:9.5px;text-align:center;line-height:26px}
h2{position:absolute;left:0;width:927px;text-align:center;font-size:14px;font-weight:700;color:var(--ink)}
.lead{position:absolute;left:0;width:927px;text-align:center;font-size:8.6px;line-height:16.5px}
.rule{position:absolute;left:132px;top:521px;width:663px;height:1px;background:var(--rule)}
.svc-sub{position:absolute;left:0;top:581px;width:927px;text-align:center;font-size:9.8px}
.svc{position:absolute;top:620px;width:165px;height:46px}
.svc-icon{position:absolute;left:0;top:0;width:42px;height:42px;border-radius:50%;background:var(--green)}
.svc-icon svg{position:absolute;left:9px;top:9px}
.svc h3{position:absolute;left:51px;top:4px;font-size:9.8px;font-weight:400;color:var(--ink);white-space:nowrap}
.svc p{position:absolute;left:51px;top:20px;font-size:8px;line-height:14.5px;width:110px}
.chev{position:absolute;font-size:16px;color:#999;transform:scaleY(1.6)}
.about-img{position:absolute;left:132px;top:722px;width:188px;height:151px;background:linear-gradient(110deg,#e9ecef 0%,#c9ced3 55%,#7c8288 100%)}
.about h2{left:343px;top:720px;width:auto;text-align:left}
.about p{position:absolute;left:343px;width:450px;font-size:8px;line-height:15.3px}
.read-more{position:absolute;left:344px;top:847px;width:82px;height:22px;background:var(--green);color:var(--white);font-size:7.5px;text-align:center;line-height:22px}
.testimonials{position:absolute;left:0;top:914px;width:927px;height:216px;background:var(--green);color:var(--white)}
.testimonials h2{color:var(--white);left:0;width:1062px;top:35px}
.portrait{position:absolute;left:173px;top:65px;width:101px;height:101px;border-radius:50%;background:radial-gradient(circle at 50% 40%,#e6d5c8 0%,#b8a89b 35%,#3d4a5e 70%,#2a3547 100%)}
.quote-text{position:absolute;left:340px;top:71px;width:382px;text-align:center;font-size:8.6px;line-height:16.5px}
.qmark{position:absolute;font-size:34px;font-style:italic;font-family:Georgia,serif;line-height:1}
.author{position:absolute;left:340px;top:147px;width:382px;text-align:center;font-size:8.2px;line-height:16.5px}
.author em{font-style:italic}
.t-chev{color:rgba(255,255,255,.8)}
.site-footer{position:absolute;left:0;top:1130px;width:927px;height:70px;background:var(--footer);color:var(--footer-text)}
.foot-nav{position:absolute;left:134px;top:19px;font-size:8px;white-space:nowrap;word-spacing:0}
.foot-nav span{margin:0 12px}
.copy{position:absolute;left:134px;top:41px;font-size:7.8px}
.social{position:absolute;top:23px;width:22px;height:22px;border-radius:50%;background:#6e6e6e}
</style>
</head>
<body>

<header class="site-header">
  <div class="brand"><span class="brand-dot"></span>Velmora Systems</div>
  <nav class="main-nav">
    <a style="left:345px">About Us</a>
    <a style="left:414px">Clients</a>
    <a style="left:492px">Services</a>
    <a style="left:575px">Supports</a>
    <a style="left:665px">Testimonials</a>
    <a style="left:760px">Contact Us</a>
  </nav>
</header>

<section class="hero" role="img" aria-label="Photo of a man in a suit inspecting a tunnel of binary code with a magnifying glass">
  <span class="hero-arrow" style="left:47px">
    <svg width="33" height="33" viewBox="0 0 33 33"><path d="M19 10 L12 16.5 L19 23" fill="none" stroke="rgba(255,255,255,.6)" stroke-width="2"/></svg>
  </span>
  <span class="hero-arrow" style="left:821px">
    <svg width="33" height="33" viewBox="0 0 33 33"><path d="M14 10 L21 16.5 L14 23" fill="none" stroke="rgba(255,255,255,.6)" stroke-width="2"/></svg>
  </span>
  <div class="remote">
    <span class="remote-label">Remote Support</span>
    <div class="remote-input">Enter your 6-digit code</div>
    <div class="remote-btn">CONNECT NOW</div>
  </div>
</section>

<section class="welcome">
  <h2 style="top:423px">WELCOME TO VELMORA SYSTEMS</h2>
  <p class="lead" style="top:450px">Velmora Systems is an Adelaide based company with a single objective - to excel in the support and service of all computer and IT needs.<br>We provide a high level of consulting services using the most experienced engineers at a reasonable and fair price. We believe in using a Business Value<br>approach to every aspect of computer consulting to provide our clients with the most cost effective solutions.</p>
</section>

<div class="rule"></div>

<section class="services">
  <h2 style="top:548px">OUR SERVICES</h2>
  <p class="svc-sub">Velmora Systems is an Adelaide based company with a single objective - to excel in the support and service of all computer and IT needs.</p>
  <span class="chev" style="left:104px;top:628px">&#x2039;</span>
  <span class="chev" style="left:807px;top:628px">&#x203A;</span>

  <div class="svc" style="left:132px">
    <div class="svc-icon"><svg width="24" height="24" viewBox="0 0 24 24"><rect x="5" y="7" width="14" height="9" fill="none" stroke="#fff" stroke-width="1.6"/><path d="M3 18 H21" stroke="#fff" stroke-width="1.8"/></svg></div>
    <h3>On-site Service</h3>
    <p>Velmora Systems is an Adelaide based company...</p>
  </div>
  <div class="svc" style="left:303px">
    <div class="svc-icon"><svg width="24" height="24" viewBox="0 0 24 24"><rect x="5" y="10" width="11" height="8" fill="none" stroke="#fff" stroke-width="1.6"/><path d="M14 4 A6 6 0 0 1 20 10 M14 7 A3 3 0 0 1 17 10" fill="none" stroke="#fff" stroke-width="1.6"/></svg></div>
    <h3>Remote Desktop Support</h3>
    <p>Velmora Systems is an Adelaide based company...</p>
  </div>
  <div class="svc" style="left:474px">
    <div class="svc-icon"><svg width="24" height="24" viewBox="0 0 24 24"><path d="M12 3 V21 M8 8 H16 M9 12 H15" stroke="#fff" stroke-width="1.8"/></svg></div>
    <h3>Medical IT Service</h3>
    <p>Velmora Systems is an Adelaide based company...</p>
  </div>
  <div class="svc" style="left:645px">
    <div class="svc-icon"><svg width="24" height="24" viewBox="0 0 24 24"><rect x="3" y="9" width="14" height="7" rx="3.5" transform="rotate(-35 10 12.5)" fill="none" stroke="#fff" stroke-width="1.6"/><circle cx="17" cy="15" r="4" fill="#fff"/></svg></div>
    <h3>Pharmacy IT Service</h3>
    <p>Velmora Systems is an Adelaide based company...</p>
  </div>
</section>

<section class="about">
  <div class="about-img" role="img" aria-label="Photo of a woman working at a desk with several computer monitors"></div>
  <h2>ABOUT VELMORA SYSTEMS</h2>
  <p style="top:746px">Velmora Systems is an Adelaide based company with a single objective - to excel in the support and service of all computer and IT needs.</p>
  <p style="top:791px">We provide a high level of consulting services using the most experienced engineers at a reasonable and fair price. We believe in using a Business Value approach to every aspect of computer consulting to provide our clients with the most cost effective solutions.</p>
  <div class="read-more">READ MORE &#187;</div>
</section>

<section class="testimonials">
  <h2>TESTIMONIALS</h2>
  <span class="chev t-chev" style="left:124px;top:99px">&#x2039;</span>
  <span class="chev t-chev" style="left:786px;top:99px">&#x203A;</span>
  <div class="portrait" role="img" aria-label="Portrait photo of the client giving the testimonial"></div>
  <span class="qmark" style="left:305px;top:66px">&#8220;</span>
  <p class="quote-text">I have always found the team extremely helpful with their advice over the phone. They also have the ability to access our computers remotely, and can rectify most problems quite swiftly. I have no hesitation in recommending Velmora Systems for all of your IT needs..</p>
  <span class="qmark" style="left:730px;top:119px">&#8221;</span>
  <p class="author">Daniel Harrow<br><em>( Carrow &amp; Linde Pharmacy Group )</em></p>
</section>

<footer class="site-footer">
  <div class="foot-nav">Home<span>|</span>About Us<span>|</span>Clients<span>|</span>Services<span>|</span>Supports<span>|</span>Testimonials<span>|</span>Contact Us</div>
  <div class="copy">&#169; 2014 Velmora Systems. All Rights Reserved.</div>
  <span class="social" style="left:630px"></span>
  <span class="social" style="left:658px"></span>
  <span class="social" style="left:686px"></span>
  <span class="social" style="left:714px"></span>
  <span class="social" style="left:742px"></span>
  <span class="social" style="left:770px"></span>
</footer>

</body>
</html>
```